New National Dermatology Group needs a business card!

We need a business card for our new national company that has 3 brands within the business:
Lumora Clinics Australia, Tessaly Clinics Australia and Corvane Clinics Australia.
We help people access dermatology services close to home throughout Australia.
We need a business card that has:
all 3 logos on it,
Our websites (there are three, listed above)
Our email (there are three, listed above)
The location of our first clinic: 41 Willow Rd Parramatta (this can then be changed for each location as required)

```html
<!DOCTYPE html>
<html lang="en">
<head>
<meta charset="utf-8">
<title>Business Card – Lumora, Tessaly &amp; Corvane Clinics Australia</title>
<link rel="stylesheet" href="https://fonts.googleapis.com/css2?family=Cinzel:wght@500&family=Cormorant+Garamond:ital,wght@1,500&family=Roboto+Condensed:wght@400;700&display=swap">
<style>
  :root{
    --green:#21b24b;
    --orange:#f0892a;
    --brown:#8a4218;
    --ink:#3a3a3a;
    --paper:#fbfbf9;
    --backdrop:#2a2a2a;
  }
  *{box-sizing:border-box;margin:0;padding:0}
  html,body{width:1200px;height:874px;overflow:hidden;background:var(--backdrop)}
  .stage{position:relative;width:1200px;height:874px}
  .card{position:absolute;background:var(--paper);border-radius:18px;overflow:hidden}
  .card-front{left:40px;top:242px;width:680px;height:389px}
  .card-back{left:770px;top:97px;width:389px;height:680px}
  .wave{position:absolute;inset:0;width:100%;height:100%}

  .holder{position:absolute;right:34px;top:76px;text-align:right;color:#fff}
  .holder-name{font-family:"Cinzel",serif;font-weight:500;font-size:26px;letter-spacing:2px;line-height:1}
  .holder-role{font-family:"Cormorant Garamond",serif;font-style:italic;font-weight:500;font-size:17px;margin-top:3px}

  .brand{position:absolute;width:212px}
  .brand-lumora{left:28px;top:166px}
  .brand-tessaly{left:250px;top:210px}
  .brand-corvane{left:462px;top:250px}

  .brand-name{font-family:"Roboto Condensed",sans-serif;font-weight:700;font-size:17px;line-height:1.2;white-space:nowrap}
  .tone-green{color:var(--green)}
  .tone-orange{color:var(--orange)}
  .tone-brown{color:var(--brown)}

  .contact{list-style:none;margin-top:9px;font-family:"Roboto Condensed",sans-serif;font-size:12.5px;color:var(--ink);line-height:1.34}
  .contact li{display:flex;align-items:flex-start;gap:6px}
  .contact svg{width:11px;height:11px;flex:none;margin-top:3px}
  .brand-lumora .contact svg{fill:var(--green)}
  .brand-tessaly .contact svg{fill:var(--orange)}
  .brand-corvane .contact svg{fill:var(--brown)}
  .contact .indent{padding-left:17px}

  .back-stack{position:absolute;left:0;right:0;top:70px;text-align:center}
  .back-brand .brand-name{font-size:27px}
  .back-brand .site{font-family:"Roboto Condensed",sans-serif;font-weight:700;font-size:14px;color:var(--ink);margin-top:8px;letter-spacing:.3px}
  .divider{width:22px;height:2px;margin:34px auto}
  .divider-green{background:var(--green)}
  .divider-orange{background:var(--orange)}
</style>
</head>
<body>
<svg width="0" height="0" style="position:absolute" aria-hidden="true">
  <symbol id="i-pin" viewBox="0 0 24 24"><path d="M12 1a8 8 0 0 0-8 8c0 6 8 14 8 14s8-8 8-14a8 8 0 0 0-8-8zm0 11a3 3 0 1 1 0-6 3 3 0 0 1 0 6z"/></symbol>
  <symbol id="i-phone" viewBox="0 0 24 24"><path d="M6.6 10.8a15 15 0 0 0 6.6 6.6l2.2-2.2a1 1 0 0 1 1-.3 11 11 0 0 0 3.6.6 1 1 0 0 1 1 1V20a1 1 0 0 1-1 1A17 17 0 0 1 3 4a1 1 0 0 1 1-1h3.5a1 1 0 0 1 1 1 11 11 0 0 0 .6 3.6 1 1 0 0 1-.3 1z"/></symbol>
  <symbol id="i-mail" viewBox="0 0 24 24"><path d="M2 5h20v14H2zm2 2v.5l8 5 8-5V7l-8 5z"/></symbol>
  <symbol id="i-globe" viewBox="0 0 24 24"><path d="M12 2a10 10 0 1 0 0 20 10 10 0 0 0 0-20zm0 2a13 13 0 0 1 1.9 4h-3.8A13 13 0 0 1 12 4zM4.3 14a8 8 0 0 1 0-4h3.4a16 16 0 0 0 0 4zM12 20a13 13 0 0 1-1.9-4h3.8A13 13 0 0 1 12 20zm2.3-6H9.7a14 14 0 0 1 0-4h4.6a14 14 0 0 1 0 4zm2 0a16 16 0 0 0 0-4h3.4a8 8 0 0 1 0 4z"/></symbol>
</svg>

<main class="stage">
  <section class="card card-front">
    <svg class="wave" viewBox="0 0 680 389" preserveAspectRatio="none" aria-hidden="true">
      <rect width="680" height="389" fill="var(--green)"/>
      <path d="M0,100 C80,66 200,52 300,84 L310,92 C210,62 90,80 0,118 Z" fill="var(--orange)"/>
      <path d="M0,118 C90,80 210,62 310,92 C410,122 470,214 580,232 C630,240 660,236 680,232 L680,389 L0,389 Z" fill="var(--brown)"/>
      <path d="M0,118 C90,80 210,62 310,92 C410,122 470,230 580,248 C630,256 660,252 680,248 L680,389 L0,389 Z" fill="var(--paper)"/>
    </svg>

    <div class="holder">
      <p class="holder-name">DANIEL HARLOW</p>
      <p class="holder-role">President</p>
    </div>

    <div class="brand brand-lumora">
      <p class="brand-name tone-green">Lumora Clinics Australia</p>
      <ul class="contact">
        <li><svg><use href="#i-pin"/></svg><span>41 Willow Rd</span></li>
        <li class="indent">Parramatta NSW 2150</li>
        <li><svg><use href="#i-phone"/></svg><span>02 5550 1874</span></li>
        <li><svg><use href="#i-mail"/></svg><span>info@lumoraclinics.com.au</span></li>
        <li><svg><use href="#i-globe"/></svg><span>lumoraclinics.com.au</span></li>
      </ul>
    </div>

    <div class="brand brand-tessaly">
      <p class="brand-name tone-orange">Tessaly Clinics Australia</p>
      <ul class="contact">
        <li><svg><use href="#i-pin"/></svg><span>41 Willow Rd</span></li>
        <li class="indent">Parramatta NSW 2150</li>
        <li><svg><use href="#i-phone"/></svg><span>02 5550 1874</span></li>
        <li><svg><use href="#i-mail"/></svg><span>info@tessalyclinics.com.au</span></li>
        <li><svg><use href="#i-globe"/></svg><span>tessalyclinics.com.au</span></li>
      </ul>
    </div>

    <div class="brand brand-corvane">
      <p class="brand-name tone-brown">Corvane Clinics Australia</p>
      <ul class="contact">
        <li><svg><use href="#i-pin"/></svg><span>41 Willow Rd</span></li>
        <li class="indent">Parramatta NSW 2150</li>
        <li><svg><use href="#i-phone"/></svg><span>02 5550 1874</span></li>
        <li><svg><use href="#i-mail"/></svg><span>info@corvaneclinics.com.au</span></li>
        <li><svg><use href="#i-globe"/></svg><span>corvaneclinics.com.au</span></li>
      </ul>
    </div>
  </section>

  <section class="card card-back">
    <svg class="wave" viewBox="0 0 389 680" preserveAspectRatio="none" aria-hidden="true">
      <path d="M220,560 C290,520 340,460 389,420 L389,432 C345,470 300,525 240,556 Z" fill="var(--orange)"/>
      <path d="M0,630 C110,625 180,592 250,552 C300,524 340,480 389,440 L389,680 L0,680 Z" fill="var(--brown)"/>
      <path d="M0,650 C120,642 180,602 250,566 C310,535 350,490 389,460 L389,680 L0,680 Z" fill="var(--green)"/>
    </svg>

    <div class="back-stack">
      <div class="back-brand">
        <p class="brand-name tone-green">Lumora Clinics Australia</p>
        <p class="site">LUMORACLINICS.COM.AU</p>
      </div>
      <div class="divider divider-green"></div>
      <div class="back-brand">
        <p class="brand-name tone-orange">Tessaly Clinics Australia</p>
        <p class="site">WWW.TESSALYCLINICS.COM.AU</p>
      </div>
      <div class="divider divider-orange"></div>
      <div class="back-brand">
        <p class="brand-name tone-brown">Corvane Clinics Australia</p>
        <p class="site">WWW.CORVANECLINICS.COM.AU</p>
      </div>
    </div>
  </section>
</main>
</body>
</html>
```